Website with a rustic Patriotic Feel

I am looking to design the
Home page I have a mock-up that has the essentials on it like our video, a small slideshow, our plans, and a coverage map, and a small sign up box to be sent a free SIM card.

Eligibility Page: Cool Background with a fill in box that lets the user know if their number is GSM or unlocked.

View Plans page: will have our plans hopefully in their colors with a cool background a walkthrough on Activation.

Activation: If you order your plan first then we send the SIM Card Basically another fill out sheet first name last name ICCID IMEI phone number email

, Contact Us: This is our Customer support page.

Steady Beacon ( this will be our About us page and will have a calendar of Community Volunteer Opportunities.. Right now I have a hodgepodge of different themes that I am going with for the web design. I would like it cohesive with the theme so all of it can fit together nicely.

At the Site map at the bottom we are looking for the basic Menu redirects. quick links to our T&Cs Customer Support and Follow US Buttons as well as a sign up for our Newsletter fill in.

Feel free to redo any of the ads. We are an MVNO like (Northpine Wireless) we provide network Voice and Data Plans our target audience is first Responders and Military. If you are wondering what that green map is its a coverage map to see where to best have coverage. Right now I have a website that uses CMS and HTML. If you are interested in doing a full redesign of our website we would love it.

Right now our website is www.tallow-linkwave.example if you need any additional information.

Target Market(s)

First Responders and Military

Coding

Coded - Design and coding required

Number of Pages Required

5+ page

Font styles to use
Sans Serif

Colors
0455a3
0493ce
f0474d
ffffff

Requirements
Must have
• Cohesive and have a powerpoint and coverage map
Should not have
• Anything flowery or kiddish

```html
<!DOCTYPE html>
<html lang="en">
<head>
<meta charset="utf-8">
<title>Valor Link Mobile — Home</title>
<link rel="stylesheet" href="https://fonts.googleapis.com/css2?family=Poppins:wght@400;500;600;700&family=Archivo+Black&family=Roboto:wght@400;500;700&family=Libre+Baskerville&display=swap">
<style>
:root{
  --navy:#1f2840;
  --navy-deep:#182033;
  --brand-blue:#0455a3;
  --sky:#0493ce;
  --red:#f0474d;
  --white:#ffffff;
  --ink:#1c1c1c;
  --muted:#6b6459;
  --parchment:#e9dcc0;
  --parchment-dark:#d9c79f;
  --offer-blue:#1c4fdc;
  --tab-blue:#1d5fb9;
  --price-blue:#1a6fc4;
  --tick-red:#e8344a;
  --footer:#0e0e0e;
  --chat-green:#22a83a;
}
*{box-sizing:border-box;margin:0;padding:0}
html,body{width:1200px;height:3397px;overflow:hidden}
body{font-family:"Poppins",sans-serif;color:var(--ink);background:var(--white)}

/* header */
.site-header{height:79px;background:var(--navy);display:flex;align-items:center;justify-content:space-between;padding:0 112px}
.brand{display:flex;align-items:center;gap:8px;color:var(--white);font-weight:700;font-size:20px;letter-spacing:.5px}
.brand-dot{width:22px;height:22px;border-radius:50%;background:var(--sky)}
.main-nav{display:flex;align-items:center;font-size:15px;color:var(--white)}
.main-nav a{color:var(--white);text-decoration:none}
.main-nav a.active{color:var(--red)}
.main-nav .sep{margin:0 11px;opacity:.8}
.account{display:flex;align-items:center;gap:5px}

/* hero */
.hero{position:relative;height:360px;background:linear-gradient(90deg,#b8343c 0%,#e9eef3 12%,#c9d6e2 45%,#8ea3b8 75%,#9fb4c7 100%)}
.slide-arrow{position:absolute;top:163px;width:32px;height:32px;border-radius:50%;background:var(--white);display:flex;align-items:center;justify-content:center}
.slide-arrow.prev{left:34px}.slide-arrow.next{right:34px}

/* feature bar */
.feature-bar{height:98px;background:var(--navy-deep);display:flex;align-items:center;justify-content:space-between;padding:0 112px;font-family:"Libre Baskerville",serif;color:var(--white);font-size:11.5px;line-height:1.9;white-space:nowrap}
.feature{display:flex;align-items:center;gap:12px;padding-right:18px;border-right:1px solid rgba(255,255,255,.25);height:56px}
.feature:last-child{border:none;padding:0}

/* parchment */
.parchment{background:radial-gradient(ellipse at 50% 40%,#f1e7cf 0%,var(--parchment) 55%,var(--parchment-dark) 100%)}
.welcome{height:645px;text-align:center;padding-top:81px}
.welcome .kicker{color:var(--sky);font-size:17px}
.welcome h1{font-size:36px;font-weight:700;margin-top:2px;letter-spacing:.5px}
.welcome p{width:950px;margin:18px auto 0;color:var(--muted);font-size:14px;line-height:28px}
.media-row{display:flex;justify-content:center;gap:17px;margin-top:45px}
.promo{width:480px;height:285px;background:linear-gradient(135deg,#f3f7fb 0%,#dfe9f3 45%,#f6f1e6 100%);box-shadow:0 2px 6px rgba(0,0,0,.25)}
.video{width:480px;height:285px;background:radial-gradient(circle at 50% 45%,#1b2b4a 0%,#0a1222 70%);position:relative;box-shadow:0 2px 6px rgba(0,0,0,.25)}
.video .play{position:absolute;left:214px;top:112px;width:52px;height:52px;border-radius:50%;background:var(--white);display:flex;align-items:center;justify-content:center}
.video .controls{position:absolute;left:0;right:0;bottom:0;height:26px;display:flex;align-items:center;gap:10px;padding:0 8px;color:var(--white);font-size:8px;font-family:"Roboto",sans-serif}
.video .progress{position:absolute;left:0;right:0;bottom:0;height:3px;background:#ccc}

/* offer */
.offer{position:relative;height:314px;background:linear-gradient(90deg,#1a47d6 0%,var(--offer-blue) 60%,#2a5ee6 100%);color:var(--white);font-family:"Archivo Black",sans-serif;text-align:center;overflow:hidden}
.offer .flags{position:absolute;right:0;top:0;width:370px;height:314px;background:linear-gradient(120deg,rgba(255,255,255,0) 0%,#d83a45 35%,#f4f4f4 55%,#1d3a9a 80%)}
.offer-copy{position:absolute;left:200px;width:720px;top:88px;line-height:1}
.offer-copy .t1{font-size:38px}
.offer-copy .t2{font-size:24px;margin-top:6px}
.offer-copy .t3{font-size:38px;margin-top:2px}
.offer-copy .t4{font-size:25px;margin-top:4px}

/* pricing + coverage */
.pricing{position:relative;height:1205px;overflow:hidden}
.section-title{position:absolute;left:0;right:0;text-align:center;font-family:"Roboto",sans-serif;font-size:38px;font-weight:500;letter-spacing:.5px;line-height:45px}
.section-title::after{content:"";display:block;width:48px;height:3px;background:var(--red);margin:10px auto 0}
.pricing-title{top:77px}
.coverage-title{top:661px}
.plans{position:absolute;left:0;top:160px;width:1200px;height:430px}
.plan{position:absolute;background:var(--white);box-shadow:0 1px 5px rgba(0,0,0,.18);text-align:center;font-family:"Roboto",sans-serif}
.plan-head{height:56px;display:flex;flex-direction:column;align-items:center;justify-content:center;font-size:16px;color:var(--white);letter-spacing:.3px}
.plan-head::before{content:"";width:26px;height:2px;background:currentColor;margin-bottom:6px;opacity:.9}
.plan .from{font-size:10px;color:#444;margin-top:20px}
.plan .price{font-size:29px;color:var(--price-blue);font-weight:500;margin-top:4px}
.plan .per{font-size:10px;color:#444;margin-top:2px}
.plan ul{list-style:none;text-align:left;margin:12px 0 0 22px;font-size:13px;color:#333}
.plan li{display:flex;align-items:center;gap:6px;height:27px}
.tick{width:11px;height:11px;border-radius:50%;background:var(--tick-red);flex:none}
.bronze{left:121px;top:42px;width:165px;height:316px}
.bronze .plan-head{background:linear-gradient(#c6b29c,#a88f73)}
.silver{left:286px;top:29px;width:177px;height:342px}
.silver .plan-head{background:linear-gradient(#f3f3f3,#cfcfcf);color:#333}
.platinum{left:735px;top:29px;width:179px;height:342px}
.platinum .plan-head{background:linear-gradient(#6b6b6b,#333)}
.diamond{left:914px;top:42px;width:165px;height:316px}
.diamond .plan-head{background:linear-gradient(#2f96dc,#0d5fa8)}
.gold{left:463px;top:0;width:272px;height:401px;z-index:2}
.gold .plan-head{height:72px;background:linear-gradient(#f2c64a,#dca620);font-size:19px}
.gold .from{font-size:12px;margin-top:26px}
.gold .price{font-size:36px}
.gold .per{font-size:12px}
.gold ul{font-size:16px;margin-left:68px;margin-top:16px}
.gold li{height:33.5px}
.gold .tick{width:14px;height:14px}
.subscribe-btn{position:absolute;left:515px;top:371px;width:168px;height:53px;border-radius:27px;background:linear-gradient(#f2c64a,#dca620);color:var(--white);font-size:18px;font-weight:500;display:flex;align-items:center;justify-content:center;z-index:3;font-family:"Roboto",sans-serif}

.coverage{position:absolute;left:100px;top:751px;display:flex;gap:9px}
.finder{width:496px;height:369px;background:var(--white);padding:5px}
.tabs{display:flex;gap:4px}
.tab{height:40px;background:var(--tab-blue);color:var(--white);font-size:12px;display:flex;align-items:center;justify-content:center;font-weight:500;white-space:nowrap}
.tab.active{background:var(--white);color:var(--tab-blue);border:2px solid var(--tab-blue);font-weight:400;font-size:13.5px}
.tab:nth-child(1){width:104px}.tab:nth-child(2){width:134px}.tab:nth-child(3){width:118px}.tab:nth-child(4){width:118px}
.locate{margin:6px 0 0;padding:16px 15px;border-bottom:1px solid #eee}
.locate-row{display:flex;justify-content:space-between;align-items:center;font-size:18px}
.locate-row .route{color:var(--tab-blue);font-size:14px}
.locate-row span.lbl{display:flex;align-items:center;gap:6px}
.search{display:flex;margin-top:8px;height:44px;border:1px solid #ddd}
.search .field{flex:1;font-size:13px;color:#888;display:flex;align-items:center;padding-left:15px}
.search .go{width:44px;background:var(--tab-blue);display:flex;align-items:center;justify-content:center}
.current{text-align:center;color:var(--tab-blue);font-size:15px;margin-top:16px}
.legend{padding:14px 15px 0;font-size:16px;color:#444;font-weight:500}
.legend div{display:flex;justify-content:space-between;align-items:center;height:35px}
.dot{width:17px;height:17px;border-radius:50%}
.finder-foot{display:flex;justify-content:space-between;padding:24px 10px 0 15px;font-size:17px;color:var(--tab-blue)}
.finder-foot b{font-style:italic;font-weight:700}
.map{width:496px;height:369px;background:linear-gradient(160deg,#c9dbe9 0%,#2f6fc0 35%,#1d5cb2 60%,#a9c7e2 100%)}

/* subscribe */
.newsletter{height:324px;background:linear-gradient(180deg,#1d2e52 0%,#2b3c5e 55%,#3a3f4c 100%);text-align:center;color:var(--white);padding-top:72px}
.newsletter h2{font-family:"Roboto",sans-serif;font-size:36px;font-weight:400;letter-spacing:.5px}
.newsletter p{font-size:17px;margin-top:14px;font-weight:500}
.news-form{display:flex;justify-content:center;gap:6px;margin-top:16px}
.news-form .email{width:387px;height:51px;border-radius:26px;background:var(--white);color:#888;font-size:13px;display:flex;align-items:center;padding-left:20px}
.news-form .go{width:164px;height:51px;border-radius:26px;background:var(--sky);display:flex;align-items:center;justify-content:center;font-size:16px;font-weight:500}

/* footer */
.site-footer{height:372px;background:var(--footer);color:var(--white);position:relative;font-size:14px}
.col{position:absolute;top:67px}
.col h4{font-size:16px;font-weight:600;margin-bottom:9px}
.col li{list-style:none;height:28.4px}
.col-main{left:112px}.col-quick{left:373px}.col-support{left:680px}.col-follow{left:998px}
.socials{display:flex;gap:8px;margin-top:2px}
.socials span{width:12px;height:12px;background:var(--white);border-radius:2px}
.chat{position:absolute;left:982px;top:232px;width:110px;height:38px;border-radius:19px;background:var(--chat-green);display:flex;align-items:center;justify-content:center;font-size:14px;font-weight:500}
.copyright{position:absolute;left:112px;top:298px;font-size:14px}
.payments{position:absolute;left:550px;top:296px;display:flex;gap:6px}
.payments span{width:43px;height:27px;background:var(--white);border-radius:3px}
</style>
</head>
<body>

<header class="site-header">
  <div class="brand"><span class="brand-dot"></span>VALOR LINK MOBILE</div>
  <nav class="main-nav">
    <a class="active" href="#">Home</a><span class="sep">|</span>
    <a href="#">View Plans</a><span class="sep">|</span>
    <a href="#">Activate Today</a><span class="sep">|</span>
    <a href="#">Contact Us</a><span class="sep">|</span>
    <a href="#">Steady Beacon</a><span class="sep">|</span>
    <a class="account" href="#"><svg width="13" height="14" viewBox="0 0 13 14"><circle cx="6.5" cy="4" r="3.5" fill="#fff"/><path d="M0 14c0-4 3-6 6.5-6S13 10 13 14z" fill="#fff"/></svg>My Account</a>
  </nav>
</header>

<section class="hero" role="img" aria-label="Slideshow banner: American flag, first responders and military service members, navy ship, rescue helicopter and jet with the Valor Link Mobile name">
  <span class="slide-arrow prev"><svg width="10" height="14"><path d="M8 1L2 7l6 6" stroke="#333" stroke-width="1.5" fill="none"/></svg></span>
  <span class="slide-arrow next"><svg width="10" height="14"><path d="M2 1l6 6-6 6" stroke="#333" stroke-width="1.5" fill="none"/></svg></span>
</section>

<section class="feature-bar">
  <div class="feature">
    <svg width="42" height="34" viewBox="0 0 42 34" fill="none" stroke="#e04a50" stroke-width="1.6"><rect x="2" y="6" width="24" height="18"/><path d="M26 12h8l6 7v5H26"/><circle cx="10" cy="27" r="3.5"/><circle cx="33" cy="27" r="3.5"/></svg>
    <div>Great Prices on Our Lines<br>Free Shipping for SIM Cards</div>
  </div>
  <div class="feature">
    <svg width="22" height="34" viewBox="0 0 22 34" fill="none" stroke="#fff" stroke-width="1.6"><rect x="2" y="2" width="18" height="30" rx="3"/><path d="M8 27h6"/></svg>
    <div>Give Us A Call<br>+1(800)555-0142</div>
  </div>
  <div class="feature">
    <svg width="44" height="30" viewBox="0 0 44 30" fill="none" stroke="#e04a50" stroke-width="1.6"><rect x="2" y="2" width="26" height="18" rx="9"/><rect x="16" y="10" width="26" height="18" rx="9"/><path d="M23 19h12M23 23h8"/></svg>
    <div>Chat With US<br>WE offer 24-hour chat support</div>
  </div>
  <div class="feature">
    <svg width="38" height="32" viewBox="0 0 38 32" fill="none" stroke="#e04a50" stroke-width="1.6"><path d="M2 10l4-8h26l4 8z"/><path d="M4 10v20h30V10"/><rect x="10" y="17" width="8" height="13"/><rect x="22" y="17" width="8" height="7"/></svg>
    <div>Nationwide Coverage<br>4G LTE High Speed Data</div>
  </div>
</section>

<div class="parchment">
  <section class="welcome">
    <div class="kicker">Welcome To</div>
    <h1>VALOR LINK MOBILE</h1>
    <p>Lorem ipsum dolor sit amet, consectetur adipiscing elit, sed do eiusmod tempor incididunt ut labore et dolore magna aliqua. Quis ipsum suspendisse ultrices gravida. Risus commodo viverra maecenas accumsan lacus vel facilisis. Lorem ipsum dolor sit amet, consectetur adipiscing elit, sed do eiusmod tempor incididunt ut labore et dolore magna aliqua.</p>
    <div class="media-row">
      <div class="promo" role="img" aria-label="Plan advert: bar chart of Bronze to Diamond data tiers with Family Plans offer — buy 3 lines get the 4th for free — and Data Plans with unlimited talk and text plus up to 30GB 4G LTE data"></div>
      <div class="video" role="img" aria-label="Video player showing the Valor Link Mobile intro video">
        <span class="play"><svg width="20" height="22"><path d="M3 1l16 10L3 21z" fill="#e0313a"/></svg></span>
        <div class="controls"><svg width="7" height="8"><path d="M0 0l7 4-7 4z" fill="#fff"/></svg>0:02 / 1:08</div>
        <div class="progress"></div>
      </div>
    </div>
  </section>

  <section class="offer">
    <div class="flags" role="img" aria-label="Waving American flags"></div>
    <div class="offer-copy">
      <div class="t1">LIMITED-TIME OFFER!</div>
      <div class="t2">Military and first responders will recieve their first</div>
      <div class="t3">2 DECEMBERS FOR FREE</div>
      <div class="t4">with a two year contract.</div>
    </div>
  </section>

  <section class="pricing">
    <h2 class="section-title pricing-title">CHOOSE PRICING PLAN</h2>
    <div class="plans">
      <div class="plan bronze">
        <div class="plan-head">BRONZE</div>
        <div class="from">STARTING FROM</div><div class="price">$20.00</div><div class="per">PER MONTH</div>
        <ul><li><span class="tick"></span>Data &amp; Voice</li><li><span class="tick"></span>Unlimited Talk</li><li><span class="tick"></span>Unlimited Text</li><li><span class="tick"></span>100MB</li><li><span class="tick"></span>4G LTE DATA</li></ul>
      </div>
      <div class="plan silver">
        <div class="plan-head">SILVER</div>
        <div class="from">STARTING FROM</div><div class="price">$25.00</div><div class="per">PER MONTH</div>
        <ul><li><span class="tick"></span>Data &amp; Voice</li><li><span class="tick"></span>Unlimited Talk</li><li><span class="tick"></span>Unlimited Text</li><li><span class="tick"></span>1GB</li><li><span class="tick"></span>4G LTE DATA</li></ul>
      </div>
      <div class="plan gold">
        <div class="plan-head">GOLD</div>
        <div class="from">STARTING FROM</div><div class="price">$35.00</div><div class="per">PER MONTH</div>
        <ul><li><span class="tick"></span>Data &amp; Voice</li><li><span class="tick"></span>Unlimited Talk</li><li><span class="tick"></span>Unlimited Text</li><li><span class="tick"></span>3GB</li><li><span class="tick"></span>4G LTE DATA</li></ul>
      </div>
      <div class="plan platinum">
        <div class="plan-head">PLATINUM</div>
        <div class="from">STARTING FROM</div><div class="price">$50.00</div><div class="per">PER MONTH</div>
        <ul><li><span class="tick"></span>Data &amp; Voice</li><li><span class="tick"></span>Unlimited Talk</li><li><span class="tick"></span>Unlimited Text</li><li><span class="tick"></span>100MB</li><li><span class="tick"></span>4G LTE DATA</li></ul>
      </div>
      <div class="plan diamond">
        <div class="plan-head">DIAMOND</div>
        <div class="from">STARTING FROM</div><div class="price">$65.00</div><div class="per">PER MONTH</div>
        <ul><li><span class="tick"></span>Data &amp; Voice</li><li><span class="tick"></span>Unlimited Talk</li><li><span class="tick"></span>Unlimited Text</li><li><span class="tick"></span>Unlimited Data</li><li><span class="tick"></span>Upto 22 GB</li></ul>
      </div>
      <div class="subscribe-btn">SUBSCRIBE</div>
    </div>

    <h2 class="section-title coverage-title">OUR COVERAGE AREAS</h2>
    <div class="coverage">
      <div class="finder">
        <div class="tabs">
          <div class="tab active">Wireless</div><div class="tab">CRESTLINE PREPAID</div><div class="tab">International</div><div class="tab">Crestline Stores</div>
        </div>
        <div class="locate">
          <div class="locate-row"><span class="lbl"><svg width="18" height="22" viewBox="0 0 18 22" fill="none" stroke="#e04a50" stroke-width="1.6"><path d="M9 20s6-6.5 6-11A6 6 0 0 0 3 9c0 4.5 6 11 6 11z"/><circle cx="9" cy="9" r="2.2"/></svg>Location</span><span class="route">My Route</span></div>
          <div class="search"><div class="field">Enter address,state or zip code</div><div class="go"><svg width="16" height="16" fill="none" stroke="#fff" stroke-width="2"><circle cx="6.5" cy="6.5" r="5"/><path d="M10.5 10.5l4 4"/></svg></div></div>
          <div class="current">&#9906; Use my current location</div>
        </div>
        <div class="legend">
          <div>Coverage<span class="dot" style="background:#e0313a;box-shadow:0 0 0 3px #c9d9ef"></span></div>
          <div>No Coverage<span class="dot" style="background:#1a7fd0"></span></div>
        </div>
        <div class="finder-foot"><span>Available <b>5G</b> Cities</span><span>Learn more about the legend</span></div>
      </div>
      <div class="map" role="img" aria-label="Coverage map of North America with covered areas of the United States shaded blue"></div>
    </div>
  </section>
</div>

<section class="newsletter" role="region" aria-label="Newsletter sign-up over a background photo of American flags on poles at dusk">
  <h2>SUBSCRIBE TODAY</h2>
  <p>Get The Latest News On Discounts &amp; Offers</p>
  <div class="news-form"><div class="email">Enter your email</div><div class="go">SUBSCRIBE</div></div>
</section>

<footer class="site-footer">
  <div class="col col-main"><h4>MAIN MENU</h4><ul><li>Home</li><li>Catalog</li><li>View Plans</li><li>Activate Today</li><li>Contact Us</li><li>Steady Beacon</li></ul></div>
  <div class="col col-quick"><h4>QUICK LINKS</h4><ul><li>Terms &amp; Conditions</li><li>Activating Your Service</li><li>Acceptable Use Policy</li><li>Wireless Privacy Policy</li><li>Coverage Map</li></ul></div>
  <div class="col col-support"><h4>CUSTOMER SUPPORT</h4><ul><li>View Plans</li><li>Contact Us</li><li>Phone: +1(800)555-0142</li></ul></div>
  <div class="col col-follow"><h4>FOLLOW US</h4><div class="socials"><span></span><span></span><span></span></div></div>
  <div class="chat">LIVE CHAT</div>
  <div class="copyright">Copyright © 2020 Valor Link Mobile All Rights Reserved</div>
  <div class="payments"><span></span><span></span><span></span><span></span><span></span><span></span><span></span><span></span><span></span><span></span><span></span></div>
</footer>

</body>
</html>
```